Modern card design needed for building development company

We are looking for a sharp modern new look for our business cards.
We are a New Zealand based company called TKR Ventures NZ LTD that specialises in subdividing large sections, housing and commercial buildings.
We have attached a photo of the current logo and would like to see it improved somehow as it looks a bit dated.
We are open to any colours.

Target Market(s)

Investors, Property buyers

Industry/Entity Type

Investment

Contact Information for Business Card

TKR VENTURES NZ LTD
www.tkrventuresnz.co.nz

Damon Whitcombe
Phone +64 21 938 104
Email dpwhitcombe@korumail.co.nz

Font styles to use
Serif
Sans Serif

Colors
0792cd
33a6d7
85cae6
6b449b
886aae
f04a50
ec1f27
f37122
f68d4d

Requirements
Must have
• Please try and make the logo more modern or if you have a similar one we would like to see it.

```html
<!DOCTYPE html>
<html lang="en">
<head>
<meta charset="utf-8">
<title>TKR Ventures NZ LTD — Business Card</title>
<link rel="stylesheet" href="https://fonts.googleapis.com/css2?family=Open+Sans:wght@400;600;700&display=swap">
<style>
  :root {
    --backdrop: #ecebe9;
    --card-light: #ffffff;
    --card-dark: #231f20;
    --ink: #1a1a1a;
    --rule: #8a8a8a;
    --gold: #f2c51b;
    --shadow: rgba(0, 0, 0, 0.12);
  }
  * { margin: 0; padding: 0; box-sizing: border-box; }
  html, body {
    width: 1200px;
    height: 900px;
    overflow: hidden;
    background: var(--backdrop);
    font-family: "Open Sans", Arial, sans-serif;
  }
  .canvas {
    position: relative;
    width: 1200px;
    height: 900px;
  }
  .card {
    position: absolute;
    border-radius: 16px;
    box-shadow: 0 6px 18px var(--shadow);
  }
  .card--front {
    left: 78px;
    top: 35px;
    width: 588px;
    height: 363px;
    background: var(--card-light);
    color: var(--ink);
    text-align: center;
  }
  .contact-name {
    position: absolute;
    top: 148px;
    left: 0;
    right: 0;
    font-size: 21px;
    font-weight: 600;
    letter-spacing: 0.5px;
    text-transform: uppercase;
  }
  .contact-rule {
    position: absolute;
    top: 190px;
    left: 211px;
    width: 184px;
    height: 1px;
    background: var(--rule);
  }
  .contact-details {
    position: absolute;
    top: 206px;
    left: 0;
    right: 0;
    list-style: none;
    font-size: 15px;
    line-height: 21px;
    text-transform: uppercase;
  }
  .card--back {
    left: 390px;
    top: 506px;
    width: 565px;
    height: 350px;
    background: var(--card-dark);
    display: flex;
    align-items: center;
    justify-content: center;
  }
  .brand {
    display: flex;
    flex-direction: column;
    align-items: center;
    gap: 22px;
    margin-top: 20px;
  }
  .brand-mark {
    width: 38px;
    height: 38px;
    background: var(--gold);
  }
  .brand-name {
    color: var(--gold);
    font-size: 30px;
    font-weight: 600;
    letter-spacing: 1px;
    text-transform: uppercase;
    text-align: center;
    line-height: 1.2;
  }
</style>
</head>
<body>
  <main class="canvas">
    <section class="card card--front" aria-label="Business card front">
      <h1 class="contact-name">Damon Whitcombe</h1>
      <div class="contact-rule"></div>
      <ul class="contact-details">
        <li>+64 21 938 104</li>
        <li>dpwhitcombe@korumail.co.nz</li>
        <li>www.tkrventuresnz.co.nz</li>
      </ul>
    </section>
    <section class="card card--back" aria-label="Business card back">
      <div class="brand">
        <div class="brand-mark"></div>
        <p class="brand-name">TKR Ventures<br>NZ LTD</p>
      </div>
    </section>
  </main>
</body>
</html>
```